RW Framewell Inc Business cards

We need business cards using our existing logo but slightly modified. Right now the logo says RW Loadbearing Masonry. We want to keep the RW part of the design, but replace the Structural Concrete portion with "FRAMEWELL". Please see the attached file.
Ideally this would be a blank template so we can add Different Names, titles, and phone numbers later.
On the one side we want only the logo and on the other side the detail. I'm attaching an example for you to see.
Please reach out with any other questions. Our address and other details will be given out once we find a design we like.

Target Market(s)

Construction Industry

```html
<!DOCTYPE html>
<html lang="en">
<head>
<meta charset="utf-8">
<title>RW Framewell Inc — Business Cards</title>
<link rel="stylesheet" href="https://fonts.googleapis.com/css2?family=Archivo:wght@500;700;800&display=swap">
<style>
  :root {
    --backdrop: #2b2624;
    --card: #1c1c1c;
    --brand-blue: #1f78c8;
    --steel-grey: #8e9094;
    --text-grey: #b9babc;
    --rule: #6d6e70;
  }
  html, body {
    margin: 0;
    padding: 0;
    width: 1200px;
    height: 842px;
    overflow: hidden;
    background: var(--backdrop);
  }
  .canvas {
    position: relative;
    width: 1200px;
    height: 842px;
    display: flex;
    align-items: center;
    justify-content: center;
    gap: 40px;
    font-family: "Archivo", Arial, sans-serif;
  }
  .card {
    position: relative;
    width: 540px;
    height: 309px;
    background: var(--card);
    box-shadow: 0 14px 30px rgba(0,0,0,0.45);
    overflow: hidden;
  }

  /* Details side */
  .band {
    position: absolute;
    left: 0;
    right: 0;
    height: 12px;
    background: var(--brand-blue);
  }
  .band--top { top: 0; }
  .band--bottom { bottom: 10px; }
  .details {
    position: absolute;
    left: 0;
    right: 0;
    top: 84px;
    text-align: center;
  }
  .details__name {
    margin: 0;
    color: var(--brand-blue);
    font-weight: 800;
    font-size: 22px;
    letter-spacing: 0.5px;
    text-transform: uppercase;
    line-height: 1.15;
  }
  .details__title {
    margin: 2px 0 0;
    color: var(--text-grey);
    font-weight: 700;
    font-size: 16px;
  }
  .details__rule {
    width: 170px;
    height: 1px;
    margin: 12px auto 12px;
    background: var(--rule);
    border: 0;
  }
  .details__contact {
    margin: 0;
    color: var(--text-grey);
    font-weight: 700;
    font-size: 17px;
    line-height: 1.25;
  }
  .details__contact--phone { font-size: 19px; }

  /* Logo side */
  .tab {
    position: absolute;
    width: 30px;
    height: 44px;
    background: var(--brand-blue);
  }
  .tab::after {
    content: "";
    position: absolute;
    top: 0;
    bottom: 0;
    width: 4px;
    background: var(--steel-grey);
  }
  .tab--left { left: 0; top: 186px; }
  .tab--left::after { right: 0; }
  .tab--right { right: 0; top: 80px; }
  .tab--right::after { left: 0; }
  .wordmark {
    position: absolute;
    inset: 0;
    display: flex;
    align-items: center;
    justify-content: center;
    gap: 12px;
  }
  .wordmark__square {
    width: 20px;
    height: 20px;
    background: var(--brand-blue);
  }
  .wordmark__name {
    margin: 0;
    color: var(--brand-blue);
    font-weight: 800;
    font-size: 36px;
    letter-spacing: 1px;
    text-transform: uppercase;
  }
</style>
</head>
<body>
  <main class="canvas">
    <section class="card card--details" aria-label="Business card, contact side">
      <div class="band band--top"></div>
      <div class="details">
        <h1 class="details__name">Ellis Brannock</h1>
        <p class="details__title">Managing Director</p>
        <hr class="details__rule">
        <p class="details__contact details__contact--phone">055-318 204 617</p>
        <p class="details__contact">info@rwframewell.com</p>
        <p class="details__contact">www.rwframewell.com</p>
      </div>
      <div class="band band--bottom"></div>
    </section>

    <section class="card card--logo" aria-label="Business card, logo side">
      <div class="tab tab--left"></div>
      <div class="wordmark">
        <span class="wordmark__square"></span>
        <p class="wordmark__name">RW Framewell</p>
      </div>
      <div class="tab tab--right"></div>
    </section>
  </main>
</body>
</html>
```